Medical centre needs a business card

We are a medcial centre in Australia, needing a new business card. Our demographic is low working class families. We are going to be renovating our premises to modernise the look and also had a new logo done a few months ago representing quality and community, and now need to update our cards. It needs to be doubled sided, with logo and contact details on the front, and appointment details on the back. . Needs to be modern and simple, easy to read. <br/><br/>Name: Kindle Grove Medical Centre <br/>Address: 512 Parmley Rd (Cnr Parmley Rd & Osgood Creek Rd),<br/>Tindarra Court Shopping Centre, Coralwood, NT 0870<br/>Ph: 08 8461 3072<br/>Tag line: Where your wellbeing comes first<br/>Website: www.kindlegrovemedicalcentre-example.com.au<br/>Online bookings also available<br/><br/>(On the back, to have 3 lines of appointments that can be written in.<br/>Day, date, time)<br/><br/>Your next appointment is on<br/>Can try “M T W Th F Sa Su _________________ at ____________ am/pm” or other combinations <br/>Please advise as soon as possible if unable to attend<br/>Cancellation fees apply if less than 2 hrs notice<br/>Online appointments available (please highlight this option by either by position, colour or font)

Target Market(s)

Lower social economic working class, young families to seniors

Industry/Entity Type

Medical Centre

Contact Information for Business Card

Kindle Grove Medical Centre
512 Parmley Rd (Cnr Parmley Rd & Osgood Creek Drive)
Tindarra Court Shopping Centre
Paralowie SA 5108
Ph: 08 8461 3072
www.kindlegrovemedicalcentre-example.com.au
Tagline line: where your wellbeing comes first
Back side is for appointments
Your next appointment is with Dr ______________
Day/date/time (Please give 3 lines of appointments)
Please advise as soon as possible if unable to attend
Cancellation fees apply if less than 2 hours notice
Online appointments available
Book online easily and conveniently (please highlight online appointments)

Font styles to use
Serif
Sans Serif

Colors

Designer to choose colors to be used in the design.

Requirements
Must have
• Modern and simple
• Easy to ready
• Induces a wellbeing feeling
• Incorporate our logo colours and feel from logo
• Induces feeling of stability and security
Nice to have
• Attract attention
• Pleasant to look at
• Feeling of innovation
Should not have
• Loud clashing colours
• Overly luxurious feeling
• Overly artistic

```html
<!DOCTYPE html>
<html lang="en">
<head>
<meta charset="utf-8">
<title>Kindle Grove Medical Centre – Business Card</title>
<link href="https://fonts.googleapis.com/css2?family=Montserrat:wght@400;500;600;700&display=swap" rel="stylesheet">
<style>
  :root{
    --blue:#0b6bb5;
    --green:#8dc63f;
    --ink:#1f1f1f;
    --paper:#ffffff;
    --stage:#e9ecef;
  }
  *{box-sizing:border-box;margin:0;padding:0}
  html,body{width:1200px;height:900px;overflow:hidden;background:var(--stage);font-family:"Montserrat",sans-serif}
  .canvas{position:relative;width:1200px;height:900px}
  .card{position:absolute;left:285px;width:630px;height:360px;background:var(--paper);border-radius:16px;overflow:hidden;box-shadow:0 6px 18px rgba(0,0,0,.12)}
  .card--back{top:60px}
  .card--front{top:470px}

  /* appointment side */
  .appt-title{position:absolute;left:60px;top:28px;width:520px;height:48px;border:1.5px solid var(--green);color:var(--blue);font-weight:700;font-size:19px;letter-spacing:2.5px;text-align:center;padding-top:11px}
  .field{position:absolute;color:var(--blue);font-weight:600;font-size:15px;display:flex;align-items:flex-end;gap:6px}
  .field .line{display:inline-block;border-bottom:1px solid var(--green);height:16px}
  .field--name{left:40px;top:88px}
  .field--date{left:40px;top:126px}
  .field--time{left:350px;top:126px}
  .days{position:absolute;left:40px;top:170px;width:555px;display:flex;justify-content:space-between;color:var(--blue);font-weight:600;font-size:13px}
  .days span{display:flex;align-items:center;gap:7px}
  .days i{display:inline-block;width:11px;height:11px;border:1.5px solid var(--green)}
  .notice{position:absolute;left:40px;top:206px;width:560px;color:var(--blue);font-size:15px;line-height:24px;letter-spacing:1.3px}
  .online-band{position:absolute;left:0;bottom:0;width:100%;height:66px;background:var(--blue);color:#fff;font-weight:500;font-size:18px;letter-spacing:7px;display:flex;align-items:center;justify-content:center}

  /* contact side */
  .person{position:absolute;left:40px;top:34px;color:var(--blue)}
  .person__name{font-weight:700;font-size:40px;letter-spacing:1.5px;line-height:46px}
  .person__role{color:var(--ink);font-size:18px;letter-spacing:1.2px;margin-top:-4px}
  .rule{position:absolute;left:34px;top:116px;width:380px;border-top:1.5px solid var(--green)}
  .address{position:absolute;left:34px;top:128px;color:var(--ink);font-size:18px;line-height:24px;letter-spacing:1px}
  .contact{position:absolute;left:18px;color:var(--ink);font-size:18px;letter-spacing:1px;display:flex;align-items:center;gap:10px}
  .contact--phone{top:212px}
  .contact--web{top:242px}
  .contact svg{width:15px;height:15px;flex:none}
  .tagline{position:absolute;left:0;width:100%;top:298px;text-align:center;color:var(--blue);font-size:21px;letter-spacing:.8px}
  .brand{position:absolute;right:26px;top:118px;width:190px;display:flex;align-items:center;gap:10px;color:var(--blue);font-weight:700;font-size:20px;line-height:24px}
  .brand__mark{width:28px;height:28px;background:var(--green);flex:none}
</style>
</head>
<body>
<main class="canvas">

  <section class="card card--back" aria-label="Appointment side">
    <div class="appt-title">YOUR NEXT APPOINTMENT</div>
    <div class="field field--name">Name : <span class="line" style="width:490px"></span></div>
    <div class="field field--date">Date : <span class="line" style="width:55px"></span>/<span class="line" style="width:55px"></span>/<span class="line" style="width:95px"></span></div>
    <div class="field field--time">Time : <span class="line" style="width:130px"></span> AM/PM</div>
    <div class="days">
      <span><i></i>MON</span><span><i></i>TUE</span><span><i></i>WED</span><span><i></i>THU</span><span><i></i>FRI</span><span><i></i>SAT</span><span><i></i>SUN</span>
    </div>
    <p class="notice">Please advise as soon as possible if unable to attend<br>Cancellation fees apply if less than 2 hours notice.</p>
    <div class="online-band">ONLINE APPOINTMENTS AVAILABLE</div>
  </section>

  <section class="card card--front" aria-label="Contact side">
    <div class="person">
      <div class="person__name">Liam Whitford</div>
      <div class="person__role">Manager</div>
    </div>
    <div class="rule"></div>
    <p class="address">512 Parmley Rd<br>Tindarra Court Shopping Centre,<br>Coralwood, NT 0870</p>
    <div class="contact contact--phone">
      <svg viewBox="0 0 24 24" aria-hidden="true"><path fill="#0b6bb5" d="M6.6 10.8a15 15 0 0 0 6.6 6.6l2.2-2.2c.3-.3.7-.4 1-.2 1.1.4 2.3.6 3.6.6.6 0 1 .4 1 1V20c0 .6-.4 1-1 1A17 17 0 0 1 3 4c0-.6.4-1 1-1h3.5c.6 0 1 .4 1 1 0 1.3.2 2.5.6 3.6.1.3 0 .7-.2 1z"/></svg>
      08 8461 3072
    </div>
    <div class="contact contact--web">
      <svg viewBox="0 0 24 24" aria-hidden="true"><g fill="none" stroke="#0b6bb5" stroke-width="2"><circle cx="12" cy="12" r="9"/><path d="M3 12h18M12 3c3 3 3 15 0 18M12 3c-3 3-3 15 0 18"/></g></svg>
      www.kindlegrovemedicalcentre-example.com.au
    </div>
    <p class="tagline">Where your wellbeing comes first</p>
    <div class="brand">
      <span class="brand__mark"></span>
      <span>Kindle Grove Medical Centre</span>
    </div>
  </section>

</main>
</body>
</html>
```